Letterhead and email signature block for school

We are a Remote School in the North West of Western Australia and I want to take our logo and use that to create a professional letter head and email signature block. A sample signature block is attached. For the Letterhead; The logo is also attached. I like the Orange and black combination of the logo, needs to include motto plus the following contact details;
PMB 4 BROOME WA
Phone: (08) 9170 3158
Fax: (08) 9170 3206
ABN: 41 287 519 302

The email signature block needs to have the following;
Dale Owen Wrenfield
Principal
Tern Ridge Hill RCS
Phone: (08) 9170 3158
Fax: (08) 9170 3206
Mobile: 0488 613 947
Email: Dale.Wrenfield@schoolnet-kx.org.au

Target Market(s)

Parents

Industry/Entity Type

Education

Contact Information for Business Card

Dale Owen Wrenfield
Principal
Tern Ridge Hill RCS
Phone: (08) 9170 3158
Fax: (08) 9170 3206
Mobile: 0488 613 947

Colors
f37122
000000

Requirements
Must have
• see breif

```html
<!DOCTYPE html>
<html lang="en">
<head>
<meta charset="utf-8">
<title>Tern Ridge Hill RCS – Stationery</title>
<link href="https://fonts.googleapis.com/css2?family=Arimo:wght@400;700&family=Lato:wght@400&display=swap" rel="stylesheet">
<style>
:root{
  --orange:#f26522;
  --black:#1a1a1a;
  --paper:#f6f5f3;
  --stage:#4b4b4b;
  --label:#f2f2f2;
  --body-text:#555;
}
*{box-sizing:border-box;margin:0;padding:0}
html,body{width:1200px;height:754px;overflow:hidden;background:var(--stage)}
body{position:relative;font-family:'Arimo',Arial,sans-serif}
.piece{position:absolute;background:var(--paper);overflow:hidden}
.piece svg.swoosh{position:absolute;inset:0;width:100%;height:100%}
.label{position:absolute;color:var(--label);font-family:'Lato',sans-serif;font-size:12px;transform:translateX(-50%)}
.brand{position:absolute;display:flex;align-items:center;gap:5px;color:var(--black);font-family:'Arimo',Arial,sans-serif;font-weight:400;white-space:nowrap}
.brand .dot{border-radius:50%;background:var(--orange);flex:none}

/* letterhead */
.letterhead{left:45px;top:27px;width:489px;height:689px}
.letterhead .brand{left:46px;top:110px;font-size:11px}
.letterhead .brand .dot{width:14px;height:14px}
.letter{position:absolute;left:50px;top:0;width:394px;font-family:'Lato',sans-serif;color:var(--body-text)}
.letter .salutation{position:absolute;top:214px;font-size:13px;color:#555}
.letter .body{position:absolute;top:231px;font-size:7.2px;line-height:11.7px}
.letter .body p{margin-bottom:11.7px}
.letter .closing{position:absolute;top:480px;font-size:7.2px}
.lh-contact{position:absolute;left:18px;bottom:15px;color:#fff;font-size:8.8px;line-height:13px}
.icon-line{display:flex;align-items:center;gap:5px}
.icon-line svg{width:8px;height:8px;fill:currentColor}

/* cards & signatures */
.card{width:225px;height:128px}
.card-front{left:609px;top:47px}
.card-back{left:609px;top:198px;background:var(--orange)}
.sig-one{left:864px;top:46px;width:282px;height:127px}
.sig-two{left:864px;top:199px;width:282px;height:126px}
.details{position:absolute;color:#fff;font-size:5.6px;line-height:8.6px}
.details .name{font-weight:700;font-size:8.5px;line-height:10px}
.details .role{font-size:6.2px;margin-bottom:4px}
.details .icon-line svg{width:5px;height:5px}
.card-front .details{left:8px;top:58px}
.sig-one .details{left:15px;top:68px}
.sig-two .details{left:11px;top:115px;transform:translateY(-100%)}
.card-front .brand{right:12px;top:56px;font-size:8px}
.sig-one .brand{right:14px;top:48px;font-size:8px}
.sig-two .brand{right:16px;top:52px;font-size:8px}
.brand.small .dot{width:9px;height:9px}
.card-back .brand{left:50%;top:50%;transform:translate(-50%,-50%);color:var(--black);font-size:11px}
.card-back .brand .dot{background:var(--black);width:12px;height:12px}
.sig-two .sig-name{position:absolute;right:16px;top:172px;transform:translateY(-172px);}
.sig-two .who{position:absolute;right:16px;top:95px;text-align:right}
.sig-two .who .name{color:var(--orange);font-weight:700;font-size:8px}
.sig-two .who .role{font-size:6px;color:#444}

/* envelope */
.envelope-back{left:604px;top:354px;width:548px;height:250px}
.flap{position:absolute;left:0;top:0;width:100%;height:92px}
.envelope-back .brand{left:50%;top:30px;transform:translateX(-50%);color:var(--black);font-size:10px}
.envelope-back .brand .dot{background:var(--black);width:11px;height:11px}
.envelope-front{left:568px;top:466px;width:550px;height:249px;box-shadow:0 1px 4px rgba(0,0,0,.25)}
.envelope-front .brand{left:44px;top:108px;font-size:10px}
.envelope-front .brand .dot{width:12px;height:12px}
.env-address{position:absolute;left:17px;bottom:28px;color:#fff;font-size:8.8px}
</style>
</head>
<body>

<!-- Letterhead -->
<section class="piece letterhead">
  <svg class="swoosh" viewBox="0 0 489 689" preserveAspectRatio="none">
    <path d="M0,538 C90,640 260,686 420,689 L0,689Z" fill="#1a1a1a"/>
    <path d="M0,548 C85,642 240,686 394,689 L0,689Z" fill="#f26522"/>
  </svg>
  <div class="brand"><span class="dot"></span>Tern Ridge Hill RCS</div>
  <div class="letter">
    <p class="salutation">Dear Mr. Hallory,</p>
    <div class="body">
      <p>Lorem ipsum dolor sit amet, consectetur adipiscing elit. Donec orci purus, luctus vitae dignissim eu, iaculis sed purus. Vivamus faucibus, ipsum nec aliquet viverra, leo mauris condimentum ligula, sit amet sagittis enim ligula quis arcu. Nam egestas tortor id nisi porttitor mattis. In tortor ante, ultricies in suscipit a, tempus non massa. Vivamus et auctor mi. Fusce vel massa nulla. Phasellus nec eros mauris, et scelerisque orci.</p>
      <p>Donec malesuada orci vitae nulla accumsan porta a id massa. Quisque accumsan iaculis magna sit amet fringilla. Maecenas consequat, magna eget tincidunt semper, odio nibh rutrum mi, id feugiat ante nisi eu risus. Vestibulum nunc orci, rhoncus a placerat in, ultricies in mi. Cras mattis varius eros, vel fringilla nisi suscipit eget. Quisque scelerisque sagittis nulla at porttitor.</p>
      <p>Sed id augue vitae urna euismod commodo aliquet a quam. Pellentesque arcu velit, cursus et malesuada ut, consequat et diam. Nullam erat sem, rhoncus id ullamcorper vitae, rhoncus et arcu. In ultricies ultricies nulla, ut rutrum nisi iaculis at. Donec eu magna a metus ornare faucibus. Fusce aliquet faucibus ultricies. Morbi semper, est id tincidunt gravida, sem arcu adipiscing lacus, ac bibendum nulla leo eu purus. Quisque nec diam sed risus consectetur a cummsan quis quis nibh. Vestibulum id purus lorem.</p>
      <p>It is a long established fact that a reader will be distracted by the readable content of a page when looking at its layout. The point of using Lorem Ipsum is that it has a more-or-less normal distribution of letters, as opposed to using 'Content here, content here', making it look like readable English. Many desktop publishing packages</p>
    </div>
    <p class="closing">Sincerely,</p>
  </div>
  <div class="lh-contact">
    <div>PMB 4 BROOME WA</div>
    <div>ABN: 41 287 519 302</div>
    <div class="icon-line"><svg viewBox="0 0 10 10"><rect x="2" y="0" width="6" height="10" rx="1"/></svg>(08) 9170 3158</div>
    <div class="icon-line"><svg viewBox="0 0 10 10"><rect x="2" y="0" width="6" height="3"/><rect x="0" y="3" width="10" height="5"/><rect x="2" y="8" width="6" height="2"/></svg>(08) 9170 3206</div>
  </div>
</section>
<div class="label" style="left:286px;top:725px">Letterhead</div>

<!-- Business card front -->
<section class="piece card card-front">
  <svg class="swoosh" viewBox="0 0 225 128" preserveAspectRatio="none">
    <path d="M0,0 L64,0 C84,60 140,114 206,128 L0,128Z" fill="#1a1a1a"/>
    <path d="M0,0 L60,0 C80,62 130,112 194,128 L0,128Z" fill="#f26522"/>
  </svg>
  <div class="details">
    <div class="name">Dale Owen Wrenfield</div>
    <div class="role">Principal</div>
    <div>Tern Ridge Hill RCS</div>
    <div class="icon-line"><svg viewBox="0 0 10 10"><path d="M0,4 Q5,0 10,4 L8,6 L6,4 L4,4 L2,6Z"/><rect x="2" y="6" width="6" height="4"/></svg>(08) 9170 3158</div>
    <div class="icon-line"><svg viewBox="0 0 10 10"><rect x="2" y="0" width="6" height="10" rx="1"/></svg>0488 613 947</div>
    <div class="icon-line"><svg viewBox="0 0 10 10"><rect x="2" y="0" width="6" height="3"/><rect x="0" y="3" width="10" height="5"/><rect x="2" y="8" width="6" height="2"/></svg>(08) 9170 3206</div>
    <div class="icon-line"><svg viewBox="0 0 10 10"><rect x="0" y="2" width="10" height="6"/></svg>Dale.Wrenfield@schoolnet-kx.org.au</div>
  </div>
  <div class="brand small"><span class="dot"></span>Tern Ridge Hill RCS</div>
</section>
<div class="label" style="left:723px;top:179px">Card Front</div>

<!-- Business card back -->
<section class="piece card card-back">
  <div class="brand"><span class="dot"></span>Tern Ridge Hill RCS</div>
</section>
<div class="label" style="left:723px;top:334px">Card Back</div>

<!-- Email signature 1 -->
<section class="piece sig-one">
  <svg class="swoosh" viewBox="0 0 282 127" preserveAspectRatio="none">
    <path d="M0,0 L94,0 C114,60 170,112 240,127 L0,127Z" fill="#1a1a1a"/>
    <path d="M0,0 L89,0 C108,62 160,112 226,127 L0,127Z" fill="#f26522"/>
  </svg>
  <div class="details" style="top:68px">
    <div class="name">Dale Owen Wrenfield</div>
    <div class="role">Principal</div>
    <div>Tern Ridge Hill RCS</div>
    <div class="icon-line"><svg viewBox="0 0 10 10"><path d="M0,4 Q5,0 10,4 L8,6 L6,4 L4,4 L2,6Z"/><rect x="2" y="6" width="6" height="4"/></svg>(08) 9170 3158</div>
    <div class="icon-line"><svg viewBox="0 0 10 10"><rect x="2" y="0" width="6" height="10" rx="1"/></svg>0488 613 947</div>
    <div class="icon-line"><svg viewBox="0 0 10 10"><rect x="2" y="0" width="6" height="3"/><rect x="0" y="3" width="10" height="5"/><rect x="2" y="8" width="6" height="2"/></svg>(08) 9170 3206</div>
    <div class="icon-line"><svg viewBox="0 0 10 10"><rect x="0" y="2" width="10" height="6"/></svg>Dale.Wrenfield@schoolnet-kx.org.au</div>
  </div>
  <div class="brand small"><span class="dot"></span>Tern Ridge Hill RCS</div>
</section>
<div class="label" style="left:1002px;top:178px">Email Signature 1</div>

<!-- Email signature 2 -->
<section class="piece sig-two">
  <svg class="swoosh" viewBox="0 0 282 126" preserveAspectRatio="none">
    <path d="M0,0 L42,0 C62,60 120,116 190,126 L0,126Z" fill="#1a1a1a"/>
    <path d="M0,0 L38,0 C56,62 110,114 176,126 L0,126Z" fill="#f26522"/>
  </svg>
  <div class="details" style="top:116px">
    <div>Tern Ridge Hill RCS</div>
    <div class="icon-line"><svg viewBox="0 0 10 10"><path d="M0,4 Q5,0 10,4 L8,6 L6,4 L4,4 L2,6Z"/><rect x="2" y="6" width="6" height="4"/></svg>(08) 9170 3158</div>
    <div class="icon-line"><svg viewBox="0 0 10 10"><rect x="2" y="0" width="6" height="10" rx="1"/></svg>0488 613 947</div>
    <div class="icon-line"><svg viewBox="0 0 10 10"><rect x="2" y="0" width="6" height="3"/><rect x="0" y="3" width="10" height="5"/><rect x="2" y="8" width="6" height="2"/></svg>(08) 9170 3206</div>
    <div class="icon-line"><svg viewBox="0 0 10 10"><rect x="0" y="2" width="10" height="6"/></svg>Dale.Wrenfield@schoolnet-kx.org.au</div>
  </div>
  <div class="brand small"><span class="dot"></span>Tern Ridge Hill RCS</div>
  <div class="who">
    <div class="name">Dale Owen Wrenfield</div>
    <div class="role">Principal</div>
  </div>
</section>
<div class="label" style="left:1002px;top:332px">Email Signature 2</div>

<!-- Envelope back -->
<section class="piece envelope-back">
  <svg class="flap" viewBox="0 0 548 92" preserveAspectRatio="none">
    <path d="M0,0 L548,0 L530,74 Q526,92 506,92 L42,92 Q22,92 18,74Z" fill="#f26522"/>
  </svg>
  <div class="brand"><span class="dot"></span>Tern Ridge Hill RCS</div>
</section>

<!-- Envelope front -->
<section class="piece envelope-front">
  <svg class="swoosh" viewBox="0 0 550 249" preserveAspectRatio="none">
    <path d="M0,138 C70,200 190,240 324,249 L0,249Z" fill="#1a1a1a"/>
    <path d="M0,146 C66,204 170,240 300,249 L0,249Z" fill="#f26522"/>
  </svg>
  <div class="brand"><span class="dot"></span>Tern Ridge Hill RCS</div>
  <div class="env-address">PMB 4 BROOME WA</div>
</section>
<div class="label" style="left:861px;top:725px">Envelope</div>

</body>
</html>
```